Business Card for a New Zealand IT Startup

I need a business card for VELTA Holdings. We are a young startup based in New Zealand working in internet marketing and web development. The design should have some element connected to New Zealand, such as wave, koru or silver fern, just don't use a kiwi bird.

```html
<!DOCTYPE html>
<html lang="en">
<head>
<meta charset="utf-8">
<title>VELTA Holdings – Business Card</title>
<link rel="stylesheet" href="https://fonts.googleapis.com/css2?family=Open+Sans:wght@400;600;700&display=swap">
<style>
  :root {
    --bg: #d8d5d1;
    --card: #1e2125;
    --blue: #2a7fd0;
    --orange: #e2582a;
    --white: #f2f2f2;
    --mark: #3a3d42;
    --wave: rgba(42, 127, 208, 0.35);
    --wave-soft: rgba(226, 88, 42, 0.25);
  }
  * { margin: 0; padding: 0; box-sizing: border-box; }
  html, body {
    width: 1200px; height: 864px; overflow: hidden;
    background: var(--bg);
    font-family: "Open Sans", Arial, sans-serif;
  }
  .canvas { position: relative; width: 1200px; height: 864px; }
  .card {
    position: absolute; left: 330px; width: 540px; height: 309px;
    background: var(--card);
    border-radius: 3px;
    box-shadow: 0 6px 18px rgba(0,0,0,.25);
    overflow: hidden;
  }
  .card--front { top: 98px; }
  .card--back { top: 457px; }

  .wave {
    position: absolute; left: 0; bottom: 0; width: 540px; height: 60px;
  }
  .wave path { fill: none; stroke-width: 2; }
  .wave .wave__line--main { stroke: var(--wave); }
  .wave .wave__line--soft { stroke: var(--wave-soft); }

  /* front */
  .brand {
    position: absolute; left: 0; right: 0; top: 100px;
    text-align: center;
  }
  .brand__name {
    display: inline-flex; align-items: center; gap: 14px;
    color: var(--blue); font-weight: 700; font-size: 36px; letter-spacing: 3px;
  }
  .brand__dot {
    width: 32px; height: 32px; border-radius: 50%; background: var(--blue);
  }
  .front__web {
    position: absolute; left: 0; right: 0; top: 200px; text-align: center;
    color: var(--white); font-size: 13px; letter-spacing: 5px;
  }

  /* back */
  .mark {
    position: absolute; left: 40px; top: 52px; width: 180px; height: 180px;
    border-radius: 50%;
    background: radial-gradient(circle at 38% 32%, #55595f, var(--mark) 55%, #26292d);
  }
  .divider {
    position: absolute; left: 256px; top: 40px; width: 2px; height: 210px;
    background: linear-gradient(to bottom, rgba(255,255,255,0), var(--white) 30%, var(--white) 70%, rgba(255,255,255,0));
  }
  .contact { position: absolute; left: 278px; top: 44px; color: var(--white); }
  .contact__name { color: var(--blue); font-weight: 700; font-size: 25px; line-height: 1; letter-spacing: .5px; }
  .contact__role { color: var(--orange); font-weight: 600; font-size: 14px; margin-top: 3px; }
  .contact__address { font-size: 13px; line-height: 18px; margin-top: 8px; }
  .contact__list { list-style: none; margin-top: 6px; font-size: 13px; line-height: 18px; }
  .contact__list li { display: flex; align-items: center; gap: 8px; }
  .contact__list svg { width: 12px; height: 12px; fill: var(--blue); flex: none; }
</style>
</head>
<body>
<main class="canvas">
  <section class="card card--front" aria-label="Card front">
    <div class="brand">
      <span class="brand__name"><span class="brand__dot"></span>VELTA HOLDINGS</span>
    </div>
    <p class="front__web">www.veltaholdings.co.nz</p>
    <svg class="wave" viewBox="0 0 540 60" aria-hidden="true">
      <path class="wave__line--main" d="M0 38 C60 18 120 18 180 38 S300 58 360 38 S480 18 540 38"/>
      <path class="wave__line--soft" d="M0 50 C60 30 120 30 180 50 S300 70 360 50 S480 30 540 50"/>
    </svg>
  </section>

  <section class="card card--back" aria-label="Card back">
    <div class="mark" role="img" aria-label="Embossed brand circle"></div>
    <div class="divider"></div>
    <div class="contact">
      <p class="contact__name">MARA TANE</p>
      <p class="contact__role">PRESIDENT</p>
      <p class="contact__address">18 Harbour Lane, Ponsonby<br>Auckland 1011, New Zealand</p>
      <ul class="contact__list">
        <li><svg viewBox="0 0 12 12"><path d="M2 1h3l1 3-1.5 1a7 7 0 0 0 2.5 2.5L8 6l3 1v3a1 1 0 0 1-1 1A9 9 0 0 1 1 2a1 1 0 0 1 1-1z"/></svg>+64 9 555 0142</li>
        <li><svg viewBox="0 0 12 12"><path d="M3 0h6a1 1 0 0 1 1 1v10a1 1 0 0 1-1 1H3a1 1 0 0 1-1-1V1a1 1 0 0 1 1-1zm0 2v7h6V2z"/></svg>+64 21 555 0198</li>
        <li><svg viewBox="0 0 12 12"><path d="M3 0h6v4H3zM1 5h10v5H9v2H3v-2H1zm3 3v3h4V8z"/></svg>+64 9 555 0167</li>
        <li><svg viewBox="0 0 12 12"><path d="M0 2h12v1L6 7 0 3zm0 2.5 6 4 6-4V10H0z"/></svg>mara@veltaholdings.co.nz</li>
        <li><svg viewBox="0 0 12 12"><circle cx="6" cy="6" r="6"/></svg>www.veltaholdings.co.nz</li>
      </ul>
    </div>
    <svg class="wave" viewBox="0 0 540 60" aria-hidden="true">
      <path class="wave__line--main" d="M0 44 C60 24 120 24 180 44 S300 64 360 44 S480 24 540 44"/>
      <path class="wave__line--soft" d="M0 54 C60 34 120 34 180 54 S300 74 360 54 S480 34 540 54"/>
    </svg>
  </section>
</main>
</body>
</html>
```